Pharmacy window design

WINDOW DIMENSIONS

4ft 8 1/2" WIDE
7ft 4 1/2" HIGH

i need a window sticker for 4 windows for the outside of a pharmacy. see attached examples. name of the pharmacy is Vista Corner

we would prefer to display products on the window signs eg. Baby care products, medicines. vitamins. fitness. veterinary, Health/ beauty etc.

Target Market(s)

Locals and Tourists

Industry/Entity Type

Pharmacy

```html
<!DOCTYPE html>
<html lang="en">
<head>
<meta charset="utf-8">
<title>Vista Corner – Pharmacy Window Banner</title>
<link rel="stylesheet" href="https://fonts.googleapis.com/css2?family=Oswald:wght@500;600&display=swap">
<style>
  :root {
    --backdrop: #5b5b5b;
    --brand-blue: #3c4ea3;
    --panel-blue: #343a8a;
    --brand-green: #76bf43;
    --white: #ffffff;
  }
  html, body {
    margin: 0;
    padding: 0;
    width: 1200px;
    height: 1200px;
    overflow: hidden;
    background: var(--backdrop);
  }
  .banner {
    position: absolute;
    left: 338px;
    top: 42px;
    width: 489px;
    height: 1099px;
    background: var(--panel-blue);
    overflow: hidden;
    box-shadow: 0 2px 6px rgba(0,0,0,0.35);
    font-family: "Oswald", "Arial Narrow", sans-serif;
  }
  .top-stripe {
    position: absolute;
    top: 0;
    height: 20px;
  }
  .top-stripe--blue { left: 0; width: 240px; background: var(--brand-blue); }
  .top-stripe--green { left: 250px; width: 239px; background: var(--brand-green); }
  .header {
    position: absolute;
    top: 20px;
    left: 0;
    width: 489px;
    height: 141px;
    background: var(--white);
    display: flex;
    align-items: center;
    justify-content: center;
    gap: 14px;
  }
  .brand-dot {
    width: 30px;
    height: 30px;
    border-radius: 50%;
    background: var(--brand-green);
  }
  .brand-name {
    font-weight: 500;
    font-size: 46px;
    color: var(--brand-blue);
    letter-spacing: 0.5px;
    line-height: 1;
  }
  .artwork {
    position: absolute;
    left: 0;
    top: 0;
  }
  .services {
    position: absolute;
    left: 11px;
    top: 182px;
    margin: 0;
    padding: 0;
    list-style: none;
  }
  .services li {
    display: flex;
    align-items: center;
    height: 56px;
    color: var(--white);
    font-weight: 500;
    font-size: 35px;
    letter-spacing: 0.2px;
  }
  .services svg { margin-right: 10px; flex: none; }
  .call-box {
    position: absolute;
    left: 186px;
    top: 1022px;
    width: 303px;
    height: 77px;
    background: var(--brand-green);
    color: var(--white);
    display: flex;
    align-items: center;
    justify-content: center;
    font-weight: 500;
    font-size: 38px;
    letter-spacing: 0.3px;
  }
</style>
</head>
<body>
  <main class="banner">
    <div class="top-stripe top-stripe--blue"></div>
    <div class="top-stripe top-stripe--green"></div>

    <header class="header">
      <span class="brand-dot"></span>
      <span class="brand-name">Vista Corner</span>
    </header>

    <svg class="artwork" width="489" height="1099" viewBox="0 0 489 1099">
      <defs>
        <linearGradient id="fill-vet" x1="0" y1="0" x2="1" y2="1">
          <stop offset="0" stop-color="#ffffff"/>
          <stop offset="0.6" stop-color="#eef3f3"/>
          <stop offset="1" stop-color="#3fb6ad"/>
        </linearGradient>
        <linearGradient id="fill-cosmetics" x1="0" y1="0" x2="0" y2="1">
          <stop offset="0" stop-color="#ffffff"/>
          <stop offset="0.55" stop-color="#e6d3bf"/>
          <stop offset="1" stop-color="#ffffff"/>
        </linearGradient>
        <linearGradient id="fill-baby" x1="0" y1="0" x2="1" y2="1">
          <stop offset="0" stop-color="#f6c6d6"/>
          <stop offset="0.6" stop-color="#fbe3ea"/>
          <stop offset="1" stop-color="#f2f0ee"/>
        </linearGradient>
        <linearGradient id="fill-fitness" x1="0" y1="0" x2="0" y2="1">
          <stop offset="0" stop-color="#8c8c8c"/>
          <stop offset="0.6" stop-color="#b3b3b3"/>
          <stop offset="1" stop-color="#e8e8e8"/>
        </linearGradient>
        <linearGradient id="fill-vitamins" x1="0" y1="0" x2="1" y2="1">
          <stop offset="0" stop-color="#e8842a"/>
          <stop offset="0.45" stop-color="#d42a2f"/>
          <stop offset="0.75" stop-color="#3aa83f"/>
          <stop offset="1" stop-color="#f0b12e"/>
        </linearGradient>
      </defs>

      <g role="img" aria-label="Photo of a veterinary medicine box">
        <polygon class="tile tile--vet" points="404,180 520,180 520,514 404,514 306,418 306,278"
                 fill="url(#fill-vet)" stroke="#ffffff" stroke-width="7"/>
      </g>
      <g role="img" aria-label="Photo of cosmetic bottles and makeup products">
        <polygon class="tile tile--cosmetics" points="46,527 186,527 282,622 282,766 186,862 46,862 -50,766 -50,622"
                 fill="url(#fill-cosmetics)" stroke="#ffffff" stroke-width="7"/>
      </g>
      <g role="img" aria-label="Photo of baby care products with towel and soap">
        <polygon class="tile tile--baby" points="398,527 560,527 560,878 398,878 302,782 302,622"
                 fill="url(#fill-baby)" stroke="#ffffff" stroke-width="7"/>
      </g>
      <g role="img" aria-label="Photo of dumbbells and a supplement tub">
        <polygon class="tile tile--fitness" points="244,822 322,822 378,878 378,954 322,1010 244,1010 188,954 188,878"
                 fill="url(#fill-fitness)" stroke="#ffffff" stroke-width="7"/>
      </g>
      <g role="img" aria-label="Illustration of colourful vitamin capsules">
        <polygon class="tile tile--vitamins" points="-10,878 86,878 186,978 186,1110 -10,1110"
                 fill="url(#fill-vitamins)" stroke="#ffffff" stroke-width="7"/>
      </g>
    </svg>

    <ul class="services">
      <li><svg width="22" height="22" viewBox="0 0 22 22"><rect x="2" y="5" width="14" height="14" fill="none" stroke="#76bf43" stroke-width="2"/><path d="M5 11 l4 4 l11 -12" fill="none" stroke="#76bf43" stroke-width="3"/></svg>Baby Care Products</li>
      <li><svg width="22" height="22" viewBox="0 0 22 22"><rect x="2" y="5" width="14" height="14" fill="none" stroke="#76bf43" stroke-width="2"/><path d="M5 11 l4 4 l11 -12" fill="none" stroke="#76bf43" stroke-width="3"/></svg>Fitness Products</li>
      <li><svg width="22" height="22" viewBox="0 0 22 22"><rect x="2" y="5" width="14" height="14" fill="none" stroke="#76bf43" stroke-width="2"/><path d="M5 11 l4 4 l11 -12" fill="none" stroke="#76bf43" stroke-width="3"/></svg>Medicines</li>
      <li><svg width="22" height="22" viewBox="0 0 22 22"><rect x="2" y="5" width="14" height="14" fill="none" stroke="#76bf43" stroke-width="2"/><path d="M5 11 l4 4 l11 -12" fill="none" stroke="#76bf43" stroke-width="3"/></svg>Vitamins</li>
      <li><svg width="22" height="22" viewBox="0 0 22 22"><rect x="2" y="5" width="14" height="14" fill="none" stroke="#76bf43" stroke-width="2"/><path d="M5 11 l4 4 l11 -12" fill="none" stroke="#76bf43" stroke-width="3"/></svg>Veterinary</li>
      <li><svg width="22" height="22" viewBox="0 0 22 22"><rect x="2" y="5" width="14" height="14" fill="none" stroke="#76bf43" stroke-width="2"/><path d="M5 11 l4 4 l11 -12" fill="none" stroke="#76bf43" stroke-width="3"/></svg>Health/ Beauty</li>
    </ul>

    <div class="call-box">Call&nbsp; 5550142836</div>
  </main>
</body>
</html>
```